Business card for law firm

Need business card for new law firm. Think confident, authoritative, conservative, but not stuffy or old-fashioned.

Contact Information for Business Card

Content for card - logo (uploaded), plus the following:

Paul Whitcombe (larger font)
Managing Partner (larger font, but not as large as name)
Level 9, 7 Ferris Lane
Sydney NSW 2000
Main Tel 02 9364 2710
Direct Tel 02 8472 3159
Email paul@qvlegal.com.au
www.qvlegal.com.au

Letterhead design should include logo plus:
Level 9, 7 Ferris Lane
Sydney NSW 2000
Tel 02 8472 3159
www.qvlegal.com.au

```html
<!DOCTYPE html>
<html lang="en">
<head>
<meta charset="UTF-8">
<title>Quayvale Lawyers – Business Card</title>
<link href="https://fonts.googleapis.com/css2?family=Libre+Baskerville:wght@400;700&family=Raleway:wght@400;500;600&display=swap" rel="stylesheet">
<style>
  :root {
    --navy: #1c2266;
    --navy-deep: #151a52;
    --white: #ffffff;
    --paper: #f4f4f6;
    --paper-shade: #e4e4e8;
    --backdrop: #d9dadf;
    --ink: #1c2266;
  }
  * { margin: 0; padding: 0; box-sizing: border-box; }
  html, body {
    width: 1200px; height: 900px; overflow: hidden;
    background: var(--backdrop);
  }
  .canvas {
    position: relative; width: 1200px; height: 900px;
  }
  .card {
    position: absolute; left: 260px;
    width: 680px; height: 400px;
    border-radius: 22px; overflow: hidden;
    box-shadow: 0 10px 28px rgba(20, 24, 60, 0.25);
  }
  .card--front {
    top: 40px;
    background: linear-gradient(160deg, var(--white) 30%, var(--paper) 70%, var(--paper-shade) 100%);
  }
  .card--back {
    top: 470px;
    background: radial-gradient(ellipse at 40% 30%, #262d7a 0%, var(--navy) 55%, var(--navy-deep) 100%);
  }

  /* front: name band */
  .name-band {
    position: absolute; left: 0; top: 38px;
    width: 560px; height: 84px;
    background: var(--navy);
    padding: 14px 0 0 40px;
    color: var(--white);
  }
  .name-band__name {
    font-family: "Libre Baskerville", serif;
    font-weight: 700; font-size: 27px;
    text-transform: uppercase; letter-spacing: 0.5px;
    line-height: 1.1;
  }
  .name-band__title {
    font-family: "Raleway", sans-serif;
    font-weight: 500; font-size: 17px;
    margin-top: 4px;
  }

  /* logo */
  .brand {
    position: absolute; display: flex; align-items: center; gap: 14px;
  }
  .brand__square {
    width: 34px; height: 34px; background: var(--navy);
  }
  .brand__name {
    font-family: "Libre Baskerville", serif;
    font-weight: 400; font-size: 30px;
    text-transform: uppercase; letter-spacing: 2px;
    color: var(--ink);
  }
  .card--front .brand { right: 40px; top: 160px; }
  .card--back .brand { left: 50%; top: 150px; transform: translateX(-50%); white-space: nowrap; }
  .card--back .brand__square { background: var(--paper-shade); }
  .card--back .brand__name { color: var(--paper-shade); }

  /* contacts */
  .contacts {
    position: absolute; left: 40px; top: 232px;
    list-style: none;
    font-family: "Raleway", sans-serif; font-weight: 500;
    font-size: 18px; color: var(--ink);
  }
  .contacts li { display: flex; align-items: center; gap: 12px; height: 27px; }
  .contacts svg { width: 15px; height: 15px; flex: none; }

  .address {
    position: absolute; right: 40px; top: 276px;
    text-align: right;
    font-family: "Raleway", sans-serif; font-weight: 500;
    font-size: 19px; line-height: 1.4; color: var(--ink);
  }

  .footer-shape { position: absolute; left: 0; bottom: 0; width: 680px; height: 70px; }
  .footer-url {
    position: absolute; right: 40px; bottom: 6px;
    font-family: "Raleway", sans-serif; font-weight: 500;
    font-size: 18px; color: var(--white);
  }

  .back-url {
    position: absolute; left: 0; right: 0; top: 250px;
    text-align: center;
    font-family: "Raleway", sans-serif; font-weight: 500;
    font-size: 20px; letter-spacing: 4px; color: var(--paper-shade);
  }
</style>
</head>
<body>
<main class="canvas">

  <section class="card card--front" aria-label="Business card front">
    <div class="name-band">
      <p class="name-band__name">Paul Whitcombe</p>
      <p class="name-band__title">Managing Partner</p>
    </div>

    <div class="brand">
      <span class="brand__square"></span>
      <span class="brand__name">Quayvale Lawyers</span>
    </div>

    <ul class="contacts">
      <li>
        <svg viewBox="0 0 16 16" aria-hidden="true"><path d="M4 1.5l2.2 2.6-1.3 1.6a9 9 0 0 0 5.4 5.4l1.6-1.3 2.6 2.2-1.4 2.2C7 14 2 9 1.8 3z" fill="none" stroke="currentColor" stroke-width="1.4" stroke-linejoin="round"/></svg>
        02 9364 2710
      </li>
      <li>
        <svg viewBox="0 0 16 16" aria-hidden="true"><rect x="4" y="1" width="8" height="14" rx="1.5" fill="none" stroke="currentColor" stroke-width="1.4"/><line x1="7" y1="12.5" x2="9" y2="12.5" stroke="currentColor" stroke-width="1.4"/></svg>
        02 8472 3159
      </li>
      <li>
        <svg viewBox="0 0 16 16" aria-hidden="true"><rect x="1" y="3" width="14" height="10" rx="1" fill="none" stroke="currentColor" stroke-width="1.4"/><path d="M1.5 3.5L8 9l6.5-5.5" fill="none" stroke="currentColor" stroke-width="1.4"/></svg>
        paul@qvlegal.com.au
      </li>
    </ul>

    <address class="address" style="font-style:normal">
      Level 9, 7 Ferris Lane<br>Sydney NSW 2000
    </address>

    <svg class="footer-shape" viewBox="0 0 680 70" preserveAspectRatio="none" aria-hidden="true">
      <path d="M0 0 L250 30 C270 33 282 36 292 44 L680 44 L680 70 L0 70 Z" fill="var(--navy)"/>
      <path d="M0 10 L240 37 C258 39 268 41 276 44" fill="none" stroke="var(--white)" stroke-width="3"/>
    </svg>
    <p class="footer-url">www.qvlegal.com.au</p>
  </section>

  <section class="card card--back" aria-label="Business card back">
    <div class="brand">
      <span class="brand__square"></span>
      <span class="brand__name">Quayvale Lawyers</span>
    </div>
    <p class="back-url">www.qvlegal.com.au</p>
  </section>

</main>
</body>
</html>
```